1. Overview of company:
Teal Q Amber Mobile solutions private Ltd is one of the leading innovators & providers of Value added services (VAS) and telecom solutions to the top telecom operators across the world. We are the pioneer of several telecom technologies and products with our solutions empowering over 40 telecom giant in 51 countries.

2. Product Overview:
Zippy tone is the most innovative voice morphing mobile app that has revolutionized the concept of IVR based offerings for telecom operators across the world. It lets you talk to your friend in a voice of your choice at just the press of a button. In addition to every call, users can now speak to their friends with background sounds of their choice.

In simple words: If person A calls person B, person A can choose the voice he wants B to listen, Words and sentences remain same just the voice changes. Person A can even activate a background sound for both of them while talking.

3. Objective of the design:
The purpose of this campaign is to establish Zippy tone as Innovative, Lively, Youthful, Fun mobile app generally used for spreading smiles via pranks. The primary objective is to persuade the audience to download and use Zippy Tone mobile app, as well as to spread and characterize this new app.

4. Product layout:
Page 1: Landing Page
- pictorial explanation, what Zippy Tone stands for

Page 2: Home Screen options
-Navigation to zippy tone
-Navigation to zippy backdrop

Page 3: Zippy Tone options
-Female
-Cartoon
-King
-Bunny

Page 4: Zippy backdrop options
-Romantic
-Airport
-Traffic
-Football
-Church
-Beach

5. Target Audience
The users of the mobile app will be teenager whose age ranges from 16-27. The demographics are not restricted to a particular country and will be present on global level.

6. Deliverable
- 4 Uncoded screen and icon for mobile app "Zippy Tone"
- Our company name is "Teal Q amber" , we would like to see designs that use Black and Green, at the same time its not mandatory.
-Design should communicate what the app stands for "Changing voice of caller"

Target Market(s)

User of the mobile app will be teenagers whose age ranges from 16-27. The demographics are not restricted to a particular country and will be present on global level. It's for masses.

Industry/Entity Type

Telecommunications

Requirements
Must have
• The design should be self explanatory, what the app stands for.
• Editable format for integration purpose.
Nice to have
• Would prefer Icons and very few words.
• Professional, elegant at the same time trendy designs.

```html
<!DOCTYPE html>
<html lang="en">
<head>
<meta charset="UTF-8">
<title>Zippy Tone – Home</title>
<link href="https://fonts.googleapis.com/css2?family=Open+Sans:wght@700&display=swap" rel="stylesheet">
<style>
  :root {
    --status-bg: #060606;
    --header-bg: #202020;
    --page-bg: #ffffff;
    --accent: #00d13a;
    --icon-light: #ffffff;
    --icon-muted: #9a9a9a;
  }
  html, body {
    margin: 0;
    padding: 0;
    width: 690px;
    height: 1200px;
    overflow: hidden;
    background: var(--page-bg);
    font-family: "Open Sans", sans-serif;
  }
  .screen {
    position: relative;
    width: 690px;
    height: 1200px;
    background: var(--page-bg);
  }
  .status-bar {
    position: absolute;
    top: 0; left: 0;
    width: 690px;
    height: 44px;
    background: var(--status-bg);
  }
  .status-bar svg { position: absolute; }
  .signal { left: 8px; top: 9px; }
  .battery { right: 10px; top: 10px; }
  .app-header {
    position: absolute;
    top: 44px; left: 0;
    width: 690px;
    height: 365px;
    background: var(--header-bg);
  }
  .menu-button { position: absolute; left: 33px; top: 27px; }
  .more-button { position: absolute; right: 30px; top: 24px; }
  .brand-name {
    position: absolute;
    top: 155px;
    left: 0;
    width: 100%;
    text-align: center;
    margin: 0;
    color: var(--accent);
    font-size: 40px;
    font-weight: 700;
    letter-spacing: 0.5px;
  }
  .mode-button {
    position: absolute;
    left: 218px;
    width: 242px;
    height: 242px;
    box-sizing: border-box;
    border: 3px solid var(--accent);
    border-radius: 50%;
    background: transparent;
    display: flex;
    align-items: center;
    justify-content: center;
    color: var(--accent);
    font-family: "Open Sans", sans-serif;
    font-size: 25px;
    font-weight: 700;
    letter-spacing: 0.6px;
    padding: 0;
  }
  .mode-voice { top: 472px; }
  .mode-backdrop { top: 778px; }
</style>
</head>
<body>
  <main class="screen">
    <div class="status-bar">
      <svg class="signal" width="42" height="22" viewBox="0 0 42 22" aria-hidden="true">
        <rect x="0" y="13" width="7" height="9" fill="var(--icon-muted)"/>
        <rect x="8.5" y="10" width="7" height="12" fill="var(--icon-muted)"/>
        <rect x="17" y="7" width="7" height="15" fill="var(--icon-muted)"/>
        <rect x="25.5" y="4" width="7" height="18" fill="var(--icon-muted)"/>
        <rect x="34" y="0" width="7" height="22" fill="var(--icon-muted)"/>
      </svg>
      <svg class="battery" width="44" height="22" viewBox="0 0 44 22" aria-hidden="true">
        <rect x="1" y="1" width="38" height="20" fill="none" stroke="var(--icon-muted)" stroke-width="2"/>
        <rect x="4.5" y="4.5" width="31" height="13" fill="var(--icon-muted)"/>
        <rect x="39" y="7" width="4" height="8" fill="var(--icon-muted)"/>
      </svg>
    </div>

    <header class="app-header">
      <svg class="menu-button" width="52" height="36" viewBox="0 0 52 36" aria-label="Menu">
        <rect x="0" y="0" width="52" height="4" fill="var(--icon-light)"/>
        <rect x="0" y="16" width="52" height="4" fill="var(--icon-light)"/>
        <rect x="0" y="32" width="52" height="4" fill="var(--icon-light)"/>
      </svg>
      <svg class="more-button" width="12" height="46" viewBox="0 0 12 46" aria-label="More options">
        <circle cx="6" cy="6" r="5.5" fill="var(--icon-light)"/>
        <circle cx="6" cy="23" r="5.5" fill="var(--icon-light)"/>
        <circle cx="6" cy="40" r="5.5" fill="var(--icon-light)"/>
      </svg>
      <h1 class="brand-name">Zippy Tone</h1>
    </header>

    <button class="mode-button mode-voice">Zippy Tone</button>
    <button class="mode-button mode-backdrop">Zippy Backdrop</button>
  </main>
</body>
</html>
```